Car rental website design for a UAE car rental company

This project is about creating a new website design for a car rental company located in Dubai (United Arab Emirates), I opened the same project a few months ago but I didn't receive a lot of appealing entries so I closed it but this time I am marking the project as guaranteed to avoid such situation again, if you have already provided a design before then please re-submit again on this project so that it is considered while reviewing all the designs

A few important things:

1- We need a simple non-complex design
2- The final deliverable would be 2 screens (PSD, JPEG ... etc), the first screen is for the home page and the second screen is for an internal page
3- The home page must have a section that end users can use to rent a car online directly from the home page instead of going into some inner pages
4- The current website is very old and not very appealing so avoid creating a similar design (www.crestvane-autos.example)
5- The name is Crestvane but the company rents normal cars (no Limousin cars will be rented) so avoid adding any fancy cars in the images/graphics used in the design, just normal end users cars
6- The expected pages would be: home, About us, Our team, Strategy, Contact us and links to social media pages
7- The attachments include the company's logo and some screens from other car rental companies that provide online rentals/payments

If you have any questions please feel free to ask and please note that we will need the designs urgently

Thanks

Target Market(s)

Dubai - United Arab Emirates

Industry/Entity Type

It Company

Number of Pages Required

2 page

Font styles to use
Sans Serif

Requirements
Must have
• Check the project details
Nice to have
Should not have

```html
<!DOCTYPE html>
<html lang="en">
<head>
<meta charset="utf-8">
<title>Crestvane – Rent a Car</title>
<link href="https://fonts.googleapis.com/css2?family=Roboto:ital,wght@0,300;0,400;0,500;1,300;1,400&family=Roboto+Condensed:wght@300;400&display=swap" rel="stylesheet">
<style>
:root{
  --red:#b5122b;
  --grey-bg:#e9e9e9;
  --text:#555;
  --text-light:#999;
  --gold:#dcb23e;
  --footer:#1c1c1c;
  --panel:rgba(20,20,20,.82);
  --field:#8d8d8d;
  --brand-grey:#7a8a86;
}
*{box-sizing:border-box;margin:0;padding:0}
html,body{width:778px;height:1200px;overflow:hidden;background:#fff}
body{position:relative;font-family:"Roboto",Arial,sans-serif;color:var(--text)}
h2{font-weight:400}
.abs{position:absolute}
.cond{font-family:"Roboto Condensed","Roboto",sans-serif;font-weight:400}

/* header */
.brand{left:46px;top:6px;width:90px;text-align:center}
.brand-square{width:26px;height:26px;border:2px solid var(--red);margin:0 auto 5px}
.brand-name{font-size:15px;color:var(--brand-grey);font-weight:400;letter-spacing:.3px}
.call{left:369px;top:17px;display:flex;align-items:center;gap:6px}
.call-icon{width:29px;height:29px;border-radius:50%;background:var(--red);border:2px solid #ddd;display:flex;align-items:center;justify-content:center}
.call-label{font-size:9px;color:#888;line-height:1.1}
.call-num{font-size:12px;color:var(--red)}
.search{left:555px;top:24px;width:166px;height:20px;border:1px solid #ddd;border-radius:2px;font-size:7px;color:#aaa;padding:6px 7px}
.search svg{position:absolute;right:6px;top:5px}

/* nav */
.nav{left:0;top:66px;width:778px;height:35px;background:var(--red)}
.nav-item{top:66px;height:35px;line-height:35px;font-size:12px;color:#fff}
.nav-item.active{background:#fff;color:var(--red);width:64px;text-align:center;left:50px}
.social-dot{width:16px;height:16px;border-radius:50%;background:#2a2a2a;top:76px}

/* hero */
.hero-photo{left:0;top:101px;width:778px;height:306px;background:linear-gradient(180deg,#6a5a66 0%,#c47a5c 40%,#e59a4a 55%,#3a3430 62%,#2a2626 100%)}
.booking{left:374px;top:101px;width:348px;height:306px;background:var(--panel)}
.booking-title{left:400px;top:128px;font-size:20px;color:#fff}
.f-label{left:374px;width:124px;text-align:right;font-size:9px;color:#ddd;font-family:"Roboto Condensed",sans-serif}
.f-input{left:516px;width:184px;height:18px;background:var(--field);border:1px solid #aaa;font-size:6px;color:#ccc;padding:5px 9px}
.book-btn{left:516px;top:356px;width:185px;height:21px;background:var(--red);color:#fff;font-size:11px;text-align:center;line-height:21px}
.hero-arrows{left:57px;top:340px}

/* featured */
.featured{left:0;top:407px;width:778px;height:387px;background:var(--grey-bg)}
.section-title{font-size:16px;color:#555}
.card{top:468px;width:208px;height:303px;background:#fff;box-shadow:0 8px 8px -6px rgba(0,0,0,.25)}
.card-photo{position:absolute;left:0;top:0;width:208px;height:122px}
.card-name{position:absolute;left:13px;top:133px;font-size:9px;color:#444}
.card-rule{position:absolute;left:13px;right:10px;top:148px;border-top:1px solid #ddd}
.card-price{position:absolute;left:13px;top:155px;font-size:7px;color:#999}
.spec{position:absolute;left:13px;top:173px;font-size:7px;color:#999;line-height:11.7px}
.spec-v{position:absolute;left:93px;top:173px;font-size:7px;color:#999;line-height:11.7px}
.card-btn{position:absolute;left:12px;top:265px;width:64px;height:20px;background:var(--red);color:#fff;font-size:8px;text-align:center;line-height:20px;border-radius:1px}

/* welcome */
.welcome-title{left:0;width:778px;top:826px;text-align:center;font-size:16px;color:#666}
.welcome-text{left:110px;width:558px;top:862px;text-align:center;font-size:8.6px;color:#999;line-height:12px;font-weight:300}

/* testimonials */
.testi{left:0;top:926px;width:778px;height:203px;background:var(--gold)}
.testi-title{left:0;width:778px;top:958px;text-align:center;font-size:16px;color:#fff}
.avatar{left:160px;top:995px;width:92px;height:92px;border-radius:50%;border:3px solid #fff;background:radial-gradient(circle at 50% 40%,#d9c4b0,#9a8a80 60%,#4a4a4a)}
.quote{left:277px;top:1015px;width:340px;font-size:8.8px;color:#fff;font-style:italic;font-weight:300;line-height:11.6px}
.quote-mark{left:266px;top:1000px;font-size:16px;color:#fff}
.quote-by{left:277px;top:1072px;font-size:8.8px;color:#fff;font-style:italic;font-weight:300}
.t-arrow{top:1028px;font-size:22px;color:#f1dca0}

/* footer */
.footer{left:0;top:1129px;width:778px;height:71px;background:var(--footer)}
.f-links{left:56px;top:1150px;font-size:8px;color:#aaa;font-weight:400}
.f-copy{left:56px;top:1167px;font-size:8px;color:#999;font-weight:400}
.nl-label{left:273px;top:1149px;font-size:8px;color:#aaa}
.nl-input{left:273px;top:1163px;width:100px;height:16px;background:#3a3a3a;font-size:6.5px;color:#888;padding:4px 7px}
.nl-btn{left:372px;top:1163px;width:44px;height:16px;background:var(--red);color:#fff;font-size:6px;text-align:center;line-height:16px}
.f-phone{left:466px;top:1150px;width:25px;height:25px;border-radius:50%;border:1px solid #777;display:flex;align-items:center;justify-content:center}
.f-call{left:497px;top:1150px;font-size:7px;color:#888}
.f-num{left:497px;top:1159px;font-size:13px;color:#aaa;font-family:"Roboto Condensed",sans-serif}
.f-soc{top:1151px;width:20px;height:20px;border-radius:50%;background:#444}
</style>
</head>
<body>

<header>
  <div class="abs brand">
    <div class="brand-square"></div>
    <div class="brand-name">Crestvane</div>
  </div>
  <div class="abs call">
    <div class="call-icon">
      <svg width="13" height="11" viewBox="0 0 13 11"><path d="M1 4 Q6.5 0 12 4 L10 5 L9 3.5 H4 L3 5 Z M3 6 H10 V10 H3 Z" fill="#fff"/></svg>
    </div>
    <div>
      <div class="call-label">Call Now</div>
      <div class="call-num">55501234</div>
    </div>
  </div>
  <div class="abs search">Search
    <svg width="10" height="10" viewBox="0 0 10 10"><circle cx="4" cy="4" r="3" fill="none" stroke="#666" stroke-width="1.4"/><path d="M6.2 6.2 9 9" stroke="#666" stroke-width="1.6"/></svg>
  </div>
</header>

<nav class="abs nav"></nav>
<div class="abs nav-item active">Home</div>
<div class="abs nav-item" style="left:126px">About us</div>
<div class="abs nav-item" style="left:194px">Our team</div>
<div class="abs nav-item" style="left:264px">Strategy</div>
<div class="abs nav-item" style="left:329px">Vehicles</div>
<div class="abs nav-item" style="left:395px">My Bookings</div>
<div class="abs nav-item" style="left:486px">Contact us</div>
<div class="abs social-dot" style="left:592px"></div>
<div class="abs social-dot" style="left:614px"></div>
<div class="abs social-dot" style="left:636px"></div>
<div class="abs social-dot" style="left:658px"></div>
<div class="abs social-dot" style="left:680px"></div>

<section>
  <div class="abs hero-photo" role="img" aria-label="Everyday sedan on a road at sunset"></div>
  <div class="abs booking"></div>
  <h2 class="abs booking-title cond">BOOKING FORM</h2>
  <div class="abs f-label" style="top:177px">PICK UP DATE</div>
  <div class="abs f-input" style="top:172px"></div>
  <div class="abs f-label" style="top:204px">PICK UP TIME</div>
  <div class="abs f-input" style="top:199px">HH &nbsp;: &nbsp;MM</div>
  <div class="abs f-label" style="top:231px">NUMBER OF PASSENGERS</div>
  <div class="abs f-input" style="top:226px"></div>
  <div class="abs f-label" style="top:258px">PICKUP LOCATIONS</div>
  <div class="abs f-input" style="top:253px"></div>
  <div class="abs f-label" style="top:284px">PHONE</div>
  <div class="abs f-input" style="top:279px"></div>
  <div class="abs f-label" style="top:311px">EMAIL</div>
  <div class="abs f-input" style="top:306px"></div>
  <div class="abs f-label" style="top:338px">SPECIAL REQUESTS</div>
  <div class="abs f-input" style="top:333px"></div>
  <div class="abs book-btn">BOOK NOW</div>
  <svg class="abs hero-arrows" width="36" height="24" viewBox="0 0 36 24"><path d="M10 1 1 12 10 23M26 1 35 12 26 23" fill="none" stroke="#fff" stroke-width="1.5"/></svg>
</section>

<section>
  <div class="abs featured"></div>
  <h2 class="abs section-title cond" style="left:56px;top:431px">FEATURED CARS</h2>
  <div class="abs" style="left:56px;top:456px;width:666px;border-top:1px solid #d5d5d5"></div>

  <article class="abs card" style="left:56px">
    <div class="card-photo" role="img" aria-label="Black sedan" style="background:linear-gradient(160deg,#cfd3d6,#7d8589 60%,#3b3f42)"></div>
    <div class="card-name">Car Name</div><div class="card-rule"></div>
    <div class="card-price">PRICE PER DAY</div>
    <div class="spec">Car type<br>Max. persons<br>Doors<br>Min. driver age<br>Gearbox<br>Air conditioning?<br>Unlimited km?</div>
    <div class="spec-v">Van<br>2<br>5<br>21<br>Manual<br>Yes<br>No</div>
    <div class="card-btn">Read More</div>
  </article>
  <article class="abs card" style="left:285px">
    <div class="card-photo" role="img" aria-label="Red sedan front view" style="background:linear-gradient(180deg,#f4f4f4,#e8e8e8 30%,#c8202a 55%,#e8e8e8 90%)"></div>
    <div class="card-name">Car Name</div><div class="card-rule"></div>
    <div class="card-price">PRICE PER DAY</div>
    <div class="spec">Car type<br>Max. persons<br>Doors<br>Min. driver age<br>Gearbox<br>Air conditioning?<br>Unlimited km?</div>
    <div class="spec-v">Van<br>2<br>5<br>21<br>Manual<br>Yes<br>No</div>
    <div class="card-btn">Read More</div>
  </article>
  <article class="abs card" style="left:514px">
    <div class="card-photo" role="img" aria-label="Silver family sedan" style="background:linear-gradient(180deg,#f2f3f5,#c9ccd0 50%,#9da2a8 75%,#e6e7ea)"></div>
    <div class="card-name">Car Name</div><div class="card-rule"></div>
    <div class="card-price">PRICE PER DAY</div>
    <div class="spec">Car type<br>Max. persons<br>Doors<br>Min. driver age<br>Gearbox<br>Air conditioning?<br>Unlimited km?</div>
    <div class="spec-v">Van<br>2<br>5<br>21<br>Manual<br>Yes<br>No</div>
    <div class="card-btn">Read More</div>
  </article>
</section>

<section>
  <h2 class="abs welcome-title cond">WELCOME TO CRESTVANE CAR - DUBAI</h2>
  <p class="abs welcome-text">Crestvane car is a fleet of everyday cars and vans in Dubai for people who need an extra car for relocation, vacation, city tours or whatever. We beat the service, and most likely also the price. And you can trust that the car you get from us is both clean and pretty!</p>
</section>

<section>
  <div class="abs testi"></div>
  <h2 class="abs testi-title cond">CLIENT TESTIMONIALS</h2>
  <div class="abs avatar" role="img" aria-label="Client portrait"></div>
  <div class="abs quote-mark">“</div>
  <p class="abs quote">Lorem ipsum dolor sit amet, consectetur adipisicing elit, sed do eiusmod tempor incididunt ut labore et dolore magna aliqua. Ut enim ad minim veniam, quis nostrud exercitation ullamco laboris nisi ut aliquip ex ea commodo consequat. Duis aute irure dolor in reprehenderit in voluptate velit esse cillum dolore eu fugiat nulla pariatur.</p>
  <div class="abs quote-by">- Morten Lien</div>
  <div class="abs t-arrow" style="left:83px">‹</div>
  <div class="abs t-arrow" style="left:680px">›</div>
</section>

<footer>
  <div class="abs footer"></div>
  <div class="abs f-links">About &nbsp;| &nbsp;Terms &nbsp;| &nbsp;Privacy Policy</div>
  <div class="abs f-copy">All Rights Reserved. Copyrights © 2014.</div>
  <div class="abs nl-label">Newsletter Signup</div>
  <div class="abs nl-input">Email Address</div>
  <div class="abs nl-btn">Subscribe</div>
  <div class="abs f-phone">
    <svg width="11" height="13" viewBox="0 0 11 13"><path d="M3 1 L5 4 L3.5 5.5 Q5 9 7.5 10 L9 8.5 L10.5 11 Q8 13 5 10.5 Q1 7 1 3 Z" fill="#888"/></svg>
  </div>
  <div class="abs f-call">Call Us:</div>
  <div class="abs f-num">044-5550-1977</div>
  <div class="abs f-soc" style="left:634px"></div>
  <div class="abs f-soc" style="left:657px"></div>
  <div class="abs f-soc" style="left:680px"></div>
  <div class="abs f-soc" style="left:703px"></div>
</footer>

</body>
</html>
```